Small corporate website template design

I need a couple templates designed for a small corporate website. The corporate site reflects the existence of the parent company which will own various brands/services that have their own websites, so it will mainly be used to present who we are, what we do, what is happening (news/events), how to contact us, link off to our other brand/service sites, as well as post information for public relations, investors, and job opportunities.

The company name is Brelvanto LLC (www.brelvanto-example.com), and the name is representative of stratified layers of interconnected digital services. The corporate site is not expected to generate a bunch of fanfare - that honor will be reserved for the externally linked brand/service sites.

The provided logo may be manipulated in color, size, shape, positioning, etc. to get it to fit with the design, but should be integrated in some way.

What we are looking for is a home page layout as well as a template for an inner page whereby the navigation/logo, etc may be diminished to some extent for the inner pages. We are also interested in reusable elements such as dividers, content containers, etc. in order to represent the types of information described above that we would like to present as described above.

We are particularly interested in consistency of design elements, conservative use of color (including consideration of accessibility concerns), judicious use of whitespace in favor of simplified messaging, and something lending itself well to internationalization/translation.

Target Market(s)

Small business owners, entrepreneurs (B2B)

Number of Pages Required

2 page

Font styles to use
Sans Serif

Requirements
Must have
• See the attached PDF with the logo concept, color swatches, and comparative sites.

```html
<!DOCTYPE html>
<html lang="en">
<head>
<meta charset="utf-8">
<title>Brelvanto LLC</title>
<link href="https://fonts.googleapis.com/css2?family=Nunito:wght@400;600;700;800&family=Open+Sans:wght@400;600;700&display=swap" rel="stylesheet">
<style>
:root{
  --orange:#f6a01a;
  --blue:#1b6fb5;
  --blue-light:#3a8fd6;
  --navy:#0c2748;
  --navy-deep:#081d38;
  --ink:#1d2330;
  --text:#6b7280;
  --line:#e3e7ee;
  --white:#ffffff;
  --dark-band:#2a2d33;
}
*{box-sizing:border-box;margin:0;padding:0}
html,body{width:1200px;height:3912px;overflow:hidden}
body{position:relative;background:var(--white);font-family:"Open Sans",Arial,sans-serif;color:var(--text)}
.abs{position:absolute}
h1,h2,h3,h4{font-family:"Nunito",Arial,sans-serif}
.btn{display:inline-block;background:var(--orange);color:var(--white);font:700 20px "Nunito",Arial,sans-serif;text-transform:uppercase;border-radius:40px;padding:18px 34px;letter-spacing:.5px;white-space:nowrap}

/* header */
.site-header{left:0;top:0;width:1200px;height:150px;background:var(--white);border-bottom:4px solid var(--blue)}
.brand{left:70px;top:44px;display:flex;align-items:center;gap:12px;font:800 30px "Nunito",Arial,sans-serif;color:var(--navy)}
.brand i{width:44px;height:44px;border-radius:50%;background:var(--orange);display:block}
.topbar{right:70px;top:14px;display:flex;align-items:center;gap:22px;font-size:15px;color:var(--ink);white-space:nowrap}
.topbar span{display:flex;align-items:center;gap:8px;white-space:nowrap}
.social{width:28px;height:28px;border-radius:50%;background:var(--blue);display:inline-block}
.main-nav{left:430px;top:88px;display:flex;align-items:center;font:600 18px "Nunito",Arial,sans-serif;color:var(--ink);white-space:nowrap}
.main-nav a{padding:0 32px;border-left:1px solid var(--line)}
.main-nav a:first-child{border-left:0}
.search{left:1088px;top:80px;width:42px;height:42px;border-radius:50%;border:2px solid var(--line)}

/* hero */
.hero{left:0;top:150px;width:1200px;height:610px;overflow:hidden;background:linear-gradient(90deg,#eef3f8 0%,#d8e3ee 45%,#a9bfd4 75%,#7f9bb6 100%)}
.hero h1{left:70px;top:130px;width:560px;font-size:50px;line-height:60px;font-weight:700;color:var(--navy)}
.hero .btn{left:70px;top:330px;padding:14px 28px}

/* about */
.about-photo{left:80px;top:780px;width:420px;height:440px;background:linear-gradient(135deg,#c9b8a6,#8a7d72 60%,#5b5550)}
.eyebrow{font:700 17px "Nunito",Arial,sans-serif;color:var(--blue)}
.section-title{font-size:44px;font-weight:800;color:var(--orange)}
.about-text{left:536px;top:840px;width:600px}
.about-text p{font-size:15px;line-height:25px;margin-top:20px}
.about-text .btn{margin-top:38px;padding:16px 34px}

/* band */
.agency-band{left:0;top:1290px;width:1200px;height:300px;background:linear-gradient(90deg,#3d3f44,#25272c 50%,#3a3c42);text-align:center}
.agency-band h2{margin-top:60px;font-size:40px;line-height:50px;font-weight:700;color:var(--orange)}
.agency-band p{width:740px;margin:16px auto 0;font-size:15px;line-height:24px;color:#d7dae0}

/* services */
.services-head{left:78px;top:1640px}
.services-head .section-title{color:var(--blue)}
.service{left:78px;width:600px;height:130px}
.service .hex{left:0;top:0}
.service h3{left:118px;top:4px;font-size:22px;font-weight:700;color:var(--navy);white-space:nowrap}
.service p{left:118px;top:38px;width:440px;font-size:14px;line-height:22px}
.service .more{left:118px;top:98px;font:700 14px "Nunito",Arial,sans-serif;color:var(--ink);display:flex;align-items:center;gap:10px;white-space:nowrap}
.service .dot{left:575px;top:48px;width:20px;height:20px;border-radius:50%;border:2px solid #c9ced6;background:var(--white)}
.service .dot.on{background:var(--navy);border-color:var(--navy)}
.services-photo{left:694px;top:1640px;width:430px;height:580px;background:linear-gradient(160deg,#e9edf1,#b9c3cc 55%,#7d8894)}

/* testimonial */
.testimonial{left:0;top:2288px;width:1200px;height:472px;background:linear-gradient(90deg,#202226,#35373c 50%,#1e2024)}
.testimonial .quote-mark{left:140px;top:58px}
.testimonial p{left:140px;top:128px;width:920px;font-size:16px;line-height:27px;color:#e3e5e9}
.testimonial .who{left:140px;top:228px;font:700 16px "Nunito",Arial,sans-serif;color:var(--orange)}
.testimonial .who span{color:#bfc3ca;font-weight:400}
.avatars{left:140px;top:316px;display:flex;gap:38px;align-items:center}
.avatars i{display:block;width:96px;height:96px;border-radius:50%;background:linear-gradient(160deg,#d9dde2,#9aa3ad);border:4px solid var(--white)}
.avatars i.active{width:116px;height:116px;border-color:var(--orange)}

/* blog */
.blog-head{left:0;top:2830px;width:1200px;text-align:center}
.blog-head .eyebrow{color:var(--navy)}
.blog-head .section-title{margin-top:4px}
.card{top:2940px;width:316px;height:384px;background:var(--white);border-radius:18px;box-shadow:0 6px 26px rgba(12,39,72,.14);padding:30px 26px}
.card .meta{font-size:13px;color:var(--ink);display:flex;justify-content:space-between;width:210px;white-space:nowrap}
.card h4{margin-top:22px;font-size:22px;line-height:28px;font-weight:800;color:var(--blue)}
.card p{margin-top:16px;font-size:14px;line-height:22px}
.card .author{position:absolute;left:26px;bottom:26px;right:26px;padding-top:22px;border-top:1px solid var(--line);display:flex;align-items:center;gap:14px;font:700 13px "Nunito",Arial,sans-serif;color:var(--ink);text-transform:uppercase}
.card .author i{display:block;width:58px;height:58px;border-radius:50%;background:linear-gradient(160deg,#c8ced6,#7e8894)}
.pager{left:540px;top:3408px;display:flex;gap:14px}
.pager span{width:46px;height:46px;border-radius:50%;display:flex;align-items:center;justify-content:center}
.pager .prev{background:var(--orange)}
.pager .next{background:var(--ink)}

/* footer */
.site-footer{left:0;top:3520px;width:1200px;height:392px;background:var(--navy)}
.site-footer h4{font-size:24px;font-weight:600;color:var(--orange)}
.footer-about{left:78px;top:50px}
.footer-about .brand-foot{margin-top:42px;display:flex;gap:18px;align-items:flex-start}
.footer-about .brand-foot i{display:block;width:60px;height:60px;border-radius:50%;background:var(--orange);flex:none}
.footer-about .brand-foot b{display:block;font:800 20px "Nunito",Arial,sans-serif;color:var(--white)}
.footer-about .brand-foot p{margin-top:6px;width:260px;font-size:13px;line-height:21px;color:#c5cfdb}
.copyright{left:78px;top:340px;font-size:13px;color:#c5cfdb;white-space:nowrap}
.divider{left:488px;top:30px;width:1px;height:340px;background:rgba(255,255,255,.2)}
.divider-dot{left:480px;top:358px;width:16px;height:16px;border-radius:50%;background:var(--orange)}
.footer-contact{left:572px;top:50px;width:560px}
.footer-contact .line{margin-top:24px;display:flex;align-items:center;gap:30px;font-size:15px;color:var(--white);white-space:nowrap}
.footer-contact .line span{display:flex;align-items:center;gap:10px}
.footer-contact .socials{margin-left:auto;display:flex;gap:8px}
.footer-contact .socials i{display:block;width:28px;height:28px;border-radius:50%;border:2px solid #8aa0bb}
.newsletter{margin-top:34px}
.signup{margin-top:22px;display:flex;gap:16px}
.signup span{width:210px;height:46px;border-radius:24px;background:var(--white);font-size:14px;color:#9aa3ad;padding:13px 18px}
.signup b{width:94px;height:46px;border-radius:24px;background:var(--orange);color:var(--white);font:700 15px "Nunito",Arial,sans-serif;display:flex;align-items:center;justify-content:center}
</style>
</head>
<body>

<header class="site-header abs">
  <div class="brand abs"><i></i>Brelvanto</div>
  <div class="topbar abs">
    <span><svg width="20" height="16" viewBox="0 0 20 16"><rect x="1" y="1" width="18" height="14" rx="2" fill="none" stroke="#1b6fb5" stroke-width="2"/><path d="M1 2l9 7 9-7" fill="none" stroke="#1b6fb5" stroke-width="2"/></svg>info@brelvanto-example.com</span>
    <span><svg width="18" height="18" viewBox="0 0 18 18"><path d="M4 1l3 4-2 2c1 2 3 4 5 5l2-2 4 3-2 3C8 16 2 10 1 4z" fill="#1b6fb5"/></svg>123-456-789</span>
    <span><i class="social"></i><i class="social"></i><i class="social"></i></span>
  </div>
  <nav class="main-nav abs"><a>Home</a><a>About</a><a>Services</a><a>News</a><a>Contact</a></nav>
  <div class="search abs"></div>
</header>

<section class="hero abs" role="img" aria-label="Businessman walking on a glass walkway above a city skyline">
  <svg class="abs" style="left:0;top:0" width="1200" height="610" viewBox="0 0 1200 610">
    <polygon points="0,0 700,0 560,610 0,610" fill="#f3f6f9" opacity=".75"/>
    <polygon points="760,0 800,0 960,610 920,610" fill="#1b6fb5"/>
    <polygon points="1100,0 1200,0 1200,90" fill="#0c2748"/>
    <polygon points="1010,610 1200,420 1200,610" fill="#0c2748"/>
  </svg>
  <h1 class="abs">Adaptive Software Technology for the Digital Revolution</h1>
  <span class="btn abs">Contact Us</span>
</section>

<div class="about-photo abs" role="img" aria-label="Team of colleagues discussing work at a laptop"></div>
<section class="about-text abs">
  <div class="eyebrow">About Us</div>
  <h2 class="section-title">Who We Are...</h2>
  <p>Lorem ipsum is simply dummy text of the printing and typesetting industry. Lorem ipsum has been the industry's standard dummy text ever since the 1500s, when an unknown printer took a galley of type and scrambled it to make a type specimen book. It has survived not only five centuries, but also the leap into electronic typesetting, remaining essentially unchanged. It was popularised in the 1960s with the release of Letraset sheets containing Lorem Ipsum passages.</p>
  <span class="btn">Read More</span>
</section>

<section class="agency-band abs" role="img" aria-label="Dark photo of a desk with charts and documents">
  <h2>A digital Marketing Agency<br>Driven by Brelvanto</h2>
  <p>Brelvanto is a digital marketing and consulting agency that's filled with research-inspired talent to work with any super-focused on lead generation.</p>
</section>

<div class="services-head abs">
  <div class="eyebrow" style="color:var(--navy)">Our Services</div>
  <h2 class="section-title">What We do</h2>
</div>

<div class="service abs" style="top:1790px">
  <svg class="hex abs" width="96" height="104" viewBox="0 0 96 104"><polygon points="48,2 93,27 93,77 48,102 3,77 3,27" fill="#0c2748"/><path d="M28 70h40M32 66V54M44 66V46M56 66V38M66 44l-24 14" stroke="#fff" stroke-width="4" fill="none"/></svg>
  <h3 class="abs">Marketing Strategy</h3>
  <p class="abs">Lorem ipsum is simply dummy text of the printing and typesetting industry. Lorem ipsum has been the industry's standard.</p>
  <span class="more abs">READ MORE <svg width="26" height="10" viewBox="0 0 26 10"><path d="M0 5h24M19 1l5 4-5 4" stroke="#1d2330" stroke-width="2" fill="none"/></svg></span>
  <i class="dot on abs"></i>
</div>
<div class="service abs" style="top:1936px">
  <svg class="hex abs" width="96" height="104" viewBox="0 0 96 104"><polygon points="48,2 93,27 93,77 48,102 3,77 3,27" fill="#3a8fd6"/><rect x="26" y="34" width="44" height="30" rx="3" fill="none" stroke="#fff" stroke-width="4"/><path d="M40 72h16M34 56l8-8 6 5 12-11" stroke="#fff" stroke-width="3" fill="none"/></svg>
  <h3 class="abs" style="color:var(--blue)">Digital Analytics</h3>
  <p class="abs">Lorem ipsum is simply dummy text of the printing and typesetting industry. Lorem ipsum has been the industry's standard.</p>
  <span class="more abs">READ MORE <svg width="26" height="10" viewBox="0 0 26 10"><path d="M0 5h24M19 1l5 4-5 4" stroke="#1d2330" stroke-width="2" fill="none"/></svg></span>
  <i class="dot abs"></i>
</div>
<div class="service abs" style="top:2082px">
  <svg class="hex abs" width="96" height="104" viewBox="0 0 96 104"><polygon points="48,2 93,27 93,77 48,102 3,77 3,27" fill="#5b8fc4"/><circle cx="42" cy="48" r="12" fill="none" stroke="#fff" stroke-width="4"/><circle cx="60" cy="62" r="8" fill="none" stroke="#fff" stroke-width="4"/><path d="M42 30v6M42 60v6M24 48h6M54 48h6" stroke="#fff" stroke-width="4"/></svg>
  <h3 class="abs" style="color:var(--blue)">Management and Optimization</h3>
  <p class="abs">Lorem ipsum is simply dummy text of the printing and typesetting industry. Lorem ipsum has been the industry's standard.</p>
  <span class="more abs">READ MORE <svg width="26" height="10" viewBox="0 0 26 10"><path d="M0 5h24M19 1l5 4-5 4" stroke="#1d2330" stroke-width="2" fill="none"/></svg></span>
  <i class="dot abs"></i>
</div>
<div class="services-photo abs" role="img" aria-label="Bright office meeting room with a team seated around a table"></div>

<section class="testimonial abs" role="img" aria-label="Dark collage of portrait photos behind a client quote">
  <svg class="quote-mark abs" width="56" height="44" viewBox="0 0 56 44"><path d="M0 44V24C0 10 8 2 22 0v8c-7 2-10 6-10 14h10v22zM34 44V24c0-14 8-22 22-24v8c-7 2-10 6-10 14h10v22z" fill="#c9ccd2"/></svg>
  <p class="abs">Lorem ipsum is simply dummy text of the printing and typesetting industry. Lorem ipsum has been the industry's standard dummy text ever since the 1500s, when an unknown printer took a galley of type and scrambled it to make a type specimen book. It has survived not only five centuries, but also the leap into electronic typesetting, remaining essentially unchanged.</p>
  <div class="who abs">Lena Orvik <span>- Manager</span></div>
  <div class="avatars abs"><i class="active"></i><i></i><i></i><i></i><i></i></div>
</section>

<div class="blog-head abs">
  <div class="eyebrow">News &amp; Updates</div>
  <h2 class="section-title">Recent Blog</h2>
</div>

<article class="card abs" style="left:80px">
  <div class="meta"><span>May 18 , 2018</span><span>2 Comments</span></div>
  <h4>Lorem Ipsum printing and typesetting industry.</h4>
  <p>Lorem Ipsum is simply dummy text of the printing and typesetting industry. Lorem Ipsum has been the industry's standard.</p>
  <div class="author"><i></i>By Mira Castell</div>
</article>
<article class="card abs" style="left:452px">
  <div class="meta"><span>May 18 , 2018</span><span>2 Comments</span></div>
  <h4>Lorem Ipsum printing and typesetting industry.</h4>
  <p>Lorem Ipsum is simply dummy text of the printing and typesetting industry. Lorem Ipsum has been the industry's standard.</p>
  <div class="author"><i></i>By Mira Castell</div>
</article>
<article class="card abs" style="left:812px">
  <div class="meta"><span>May 18 , 2018</span><span>2 Comments</span></div>
  <h4>Lorem Ipsum printing and typesetting industry.</h4>
  <p>Lorem Ipsum is simply dummy text of the printing and typesetting industry. Lorem Ipsum has been the industry's standard.</p>
  <div class="author"><i></i>By Mira Castell</div>
</article>

<div class="pager abs">
  <span class="prev"><svg width="14" height="16" viewBox="0 0 14 16"><path d="M11 2L3 8l8 6" stroke="#fff" stroke-width="3" fill="none"/></svg></span>
  <span class="next"><svg width="14" height="16" viewBox="0 0 14 16"><path d="M3 2l8 6-8 6" stroke="#fff" stroke-width="3" fill="none"/></svg></span>
</div>

<footer class="site-footer abs">
  <div class="footer-about abs">
    <h4>About Company</h4>
    <div class="brand-foot"><i></i><div><b>Brelvanto</b><p>Lorem ipsum is simply dummy text of the printing and typesetting industry. Lorem ipsum has been the industry's standard.</p></div></div>
  </div>
  <div class="copyright abs">© Brelvanto LLC - 2018. All Rights Reserved</div>
  <div class="divider abs"></div>
  <div class="divider-dot abs"></div>
  <div class="footer-contact abs">
    <h4>Contact Us</h4>
    <div class="line">
      <span><svg width="20" height="16" viewBox="0 0 20 16"><rect x="1" y="1" width="18" height="14" rx="2" fill="none" stroke="#fff" stroke-width="2"/><path d="M1 2l9 7 9-7" fill="none" stroke="#fff" stroke-width="2"/></svg>info@brelvanto-example.com</span>
      <span><svg width="18" height="18" viewBox="0 0 18 18"><path d="M4 1l3 4-2 2c1 2 3 4 5 5l2-2 4 3-2 3C8 16 2 10 1 4z" fill="#fff"/></svg>123-456-789</span>
      <div class="socials"><i></i><i></i><i></i></div>
    </div>
    <h4 class="newsletter">Newsletter Sign up</h4>
    <div class="signup"><span>Name</span><span>Email</span><b>SEND</b></div>
  </div>
</footer>

</body>
</html>
```